New Business Card Design Project LORVANTI-Italy

we are LORVANTI-Italy
our company in the market for 3 years we are luxury cosmetic company and its about time for a facelift :)
i will like to have elegant luxurious and unique business card
that will give the person that get it a unique, luxurious and elegant impression
I'm VERY OPEN FOR NEW IDEAS , even duo i add a few files of things that i see on line and i like them

i add my logo as well
my website is LORVANTI.COM
(if you would like to see the main style that we have)

Target Market(s)

adult that have money :)

Industry/Entity Type

Business

Contact Information for Business Card

Name - Dario Lorvanti
Position - CEO and CO Founder
address - 4817 E Halvern
telephone - 555-384-1926
email - dario@lorvanti.com
fax - 555-384-1926
website - LORVANTI.COM

Colors
000000
959595
fbee3e
ffffff

Requirements
Must have
• big logo in GOLD color
• elegant look
• impressive
Nice to have
• not must but maybe classy pattern background
• not must but maybe emblem
• maybe clear plastic business card
Should not have
• colors
• images

```html
<!DOCTYPE html>
<html lang="en">
<head>
<meta charset="utf-8">
<title>LORVANTI Italy – Business Card</title>
<link rel="stylesheet" href="https://fonts.googleapis.com/css2?family=Source+Sans+3:wght@400;600&display=swap">
<style>
  :root {
    --backdrop: #3a3431;
    --card-black: #0b0b0b;
    --silver: #c9c9c9;
    --silver-dim: #959595;
    --gold: #d8ad3f;
    --gold-light: #e9c45a;
  }
  * { box-sizing: border-box; margin: 0; padding: 0; }
  html, body {
    width: 1200px;
    height: 864px;
    overflow: hidden;
    background: var(--backdrop);
    font-family: "Source Sans 3", "Myriad Pro", sans-serif;
  }
  .canvas {
    width: 1200px;
    height: 864px;
    display: flex;
    align-items: center;
    justify-content: center;
    gap: 48px;
  }
  .card {
    width: 520px;
    height: 297px;
    background: var(--card-black);
    border-radius: 3px;
    box-shadow: 0 14px 30px rgba(0,0,0,0.45);
    position: relative;
  }

  /* Front */
  .card-front {
    display: flex;
    flex-direction: column;
    align-items: center;
    justify-content: center;
  }
  .brand-mark {
    width: 58px;
    height: 58px;
    border-radius: 50%;
    border: 3px solid var(--silver);
    margin-bottom: 16px;
  }
  .brand-name {
    font-size: 40px;
    font-weight: 400;
    letter-spacing: 2px;
    color: var(--silver);
    line-height: 1;
  }
  .brand-rule {
    width: 190px;
    height: 2px;
    background: var(--silver);
    margin: 8px 0 6px;
  }
  .brand-origin {
    font-size: 13px;
    letter-spacing: 3px;
    color: var(--silver);
  }
  .front-web {
    margin-top: 26px;
    font-size: 14px;
    letter-spacing: 4px;
    color: var(--silver-dim);
  }

  /* Back */
  .card-back {
    display: flex;
    flex-direction: column;
    align-items: center;
    padding-top: 50px;
  }
  .back-mark {
    width: 76px;
    height: 76px;
    border-radius: 50%;
    border: 4px solid var(--gold);
  }
  .back-brand {
    margin-top: 10px;
    font-size: 22px;
    font-weight: 400;
    letter-spacing: 3px;
    color: var(--gold);
  }
  .contact {
    margin-top: 18px;
    text-align: center;
    color: var(--gold);
    line-height: 1.4;
  }
  .contact-name {
    font-size: 17px;
  }
  .contact-name strong {
    font-weight: 600;
    color: var(--gold-light);
  }
  .contact-line {
    font-size: 12.5px;
  }
</style>
</head>
<body>
  <main class="canvas">
    <section class="card card-front" aria-label="Card front">
      <div class="brand-mark"></div>
      <div class="brand-name">LORVANTI</div>
      <div class="brand-rule"></div>
      <div class="brand-origin">ITALY</div>
      <div class="front-web">www.lorvanti.com</div>
    </section>

    <section class="card card-back" aria-label="Card back">
      <div class="back-mark"></div>
      <div class="back-brand">LORVANTI</div>
      <div class="contact">
        <p class="contact-name"><strong>Dario Lorvanti</strong> - CEO &amp; CO Founder</p>
        <p class="contact-line">4817 E Halvern | P : 555-384-1926 &nbsp;F : 555-384-1926</p>
        <p class="contact-line">E : dario@lorvanti.com &nbsp;W : LORVANTI.COM</p>
      </div>
    </section>
  </main>
</body>
</html>
```